Redesign of Form/Document Navigation Page

I need a redesign of our document and navigation bar on the left. We want the same navigation bar layout/setup but want the buttons and typography to be simple and matching all over. The form needs to be aesthetically pleasing and fit within the page.

1st attachment is our Direct Deposit and the second is the form continued.

```html
<!DOCTYPE html>
<html lang="en">
<head>
<meta charset="utf-8">
<title>Direct Deposit Authorization – Sentinel Crest Security</title>
<link href="https://fonts.googleapis.com/css2?family=Open+Sans:wght@400;600&family=Roboto:wght@400;500&display=swap" rel="stylesheet">
<style>
  :root {
    --brand-blue: #2b63ad;
    --brand-blue-dark: #2d5d9e;
    --brand-yellow: #f5df75;
    --brand-gold: #e8b01e;
    --page-bg: #ebebeb;
    --panel-bg: #ffffff;
    --border: #d6d6d6;
    --text: #333333;
    --scroll-track: #f1f1f1;
    --scroll-thumb: #c8c8c8;
  }
  * { box-sizing: border-box; margin: 0; padding: 0; }
  html, body { width: 1200px; height: 951px; overflow: hidden; }
  body { position: relative; background: var(--page-bg); font-family: "Open Sans", sans-serif; color: var(--text); }

  .site-header { position: absolute; left: 0; top: 0; width: 1200px; height: 105px; background: #fff; border-bottom: 2px solid var(--brand-blue); }
  .brand { position: absolute; left: 99px; top: 32px; display: flex; align-items: center; gap: 8px; }
  .brand-mark { width: 40px; height: 40px; border-radius: 50%; background: var(--brand-gold); }
  .brand-name { font-family: "Roboto", sans-serif; font-weight: 500; font-size: 21px; line-height: 22px; color: var(--brand-gold); width: 150px; }
  .top-nav { position: absolute; right: 100px; top: 44px; display: flex; align-items: center; font-family: "Open Sans", sans-serif; font-weight: 600; font-size: 14px; color: #222; }
  .top-nav .sep { margin: 0 22px 0 24px; font-weight: 400; }
  .top-nav .user { margin-left: 38px; margin-right: 10px; }
  .power { width: 29px; height: 29px; border-radius: 50%; background: var(--brand-blue); display: flex; align-items: center; justify-content: center; }

  .side-nav { position: absolute; left: 99px; top: 147px; width: 257px; background: #fff; border: 1px solid var(--border); padding: 1px; }
  .side-nav a { display: flex; align-items: center; height: 55px; margin-bottom: 2px; padding-left: 13px; background: var(--brand-blue); color: #fff; text-decoration: none; font-family: "Roboto", sans-serif; font-weight: 500; font-size: 17px; }
  .side-nav a:last-child { margin-bottom: 0; }
  .side-nav a.back { height: 56px; background: var(--brand-yellow); color: var(--brand-blue); font-weight: 400; font-size: 17.5px; padding-left: 12px; }
  .side-nav a.back svg { margin-right: 10px; }
  .nav-icon { width: 33px; height: 33px; border-radius: 50%; background: var(--brand-yellow); display: flex; align-items: center; justify-content: center; margin-right: 10px; flex-shrink: 0; }

  .form-panel { position: absolute; left: 372px; top: 147px; width: 729px; height: 716px; background: var(--panel-bg); border: 1px solid var(--border); overflow: hidden; }
  .scrollbar { position: absolute; right: 1px; top: 1px; width: 16px; height: 712px; background: var(--scroll-track); }
  .scrollbar .thumb { position: absolute; left: 3px; top: 26px; width: 10px; height: 243px; background: var(--scroll-thumb); }
  .scrollbar .arrow { position: absolute; left: 4px; width: 0; height: 0; border-left: 4px solid transparent; border-right: 4px solid transparent; }
  .scrollbar .up { top: 8px; border-bottom: 5px solid #888; }
  .scrollbar .down { bottom: 8px; border-top: 5px solid #888; }

  .form-content { position: absolute; left: 14px; top: 20px; width: 680px; }
  .form-title { font-family: "Roboto", sans-serif; font-size: 15.5px; color: var(--brand-blue); margin-bottom: 11px; }
  .terms p { font-size: 13px; line-height: 22.3px; text-align: justify; margin-bottom: 8px; }
  .sign-row { display: flex; gap: 23px; margin-top: 18px; }
  .field label { display: block; font-family: "Roboto", sans-serif; font-size: 15.5px; color: #333; margin-bottom: 9px; }
  .field .input { width: 201px; height: 33px; border: 1px solid #bbb; background: #fff; }
  .accept-btn { margin-top: 23px; width: 203px; height: 42px; background: var(--brand-blue); color: #fff; border: 0; border-radius: 2px; font-family: "Roboto", sans-serif; font-weight: 500; font-size: 15px; }

  .manager-box { margin-top: 32px; width: 685px; height: 241px; border: 2px solid #ddd; position: relative; }
  .manager-box h2 { font-family: "Roboto", sans-serif; font-weight: 400; font-size: 17.5px; color: var(--brand-blue); text-align: center; margin-top: 20px; }
  .manager-box .col-left { position: absolute; left: 10px; top: 67px; }
  .manager-box .col-left .field + .field { margin-top: 13px; }
  .manager-box .col-right { position: absolute; left: 228px; top: 67px; }
  .manager-box .textarea { width: 441px; height: 111px; border: 1px solid #bbb; }

  .site-footer { position: absolute; left: 0; top: 902px; width: 1200px; height: 49px; background: var(--brand-blue-dark); color: #fff; font-size: 15px; font-weight: 600; text-align: center; line-height: 49px; }
</style>
</head>
<body>
  <header class="site-header">
    <div class="brand">
      <span class="brand-mark"></span>
      <span class="brand-name">SENTINEL CREST SECURITY</span>
    </div>
    <nav class="top-nav">
      <span>Home</span><span class="sep">|</span><span>Help</span>
      <span class="user">Dana Ellis</span>
      <span class="power"><svg width="15" height="15" viewBox="0 0 16 16" fill="none" stroke="#fff" stroke-width="2" stroke-linecap="round"><path d="M8 1.5v6"/><path d="M4.3 4a5.5 5.5 0 1 0 7.4 0"/></svg></span>
    </nav>
  </header>

  <nav class="side-nav">
    <a class="back" href="#"><svg width="16" height="14" viewBox="0 0 16 14" fill="#2b63ad"><path d="M7 0 0 7l7 7V9h9V5H7z"/></svg>BACK TO PROFILE</a>
    <a href="#"><span class="nav-icon"><svg width="18" height="12" viewBox="0 0 18 12"><rect x="1" y="1" width="16" height="10" fill="none" stroke="#2b63ad" stroke-width="2"/><circle cx="9" cy="6" r="2.5" fill="#2b63ad"/></svg></span>Direct Deposit</a>
    <a href="#"><span class="nav-icon"><svg width="16" height="14" viewBox="0 0 16 14" fill="none" stroke="#2b63ad" stroke-width="2"><path d="M1 3h4l6 8h4M1 11h4l6-8h4"/></svg></span>Change W-4</a>
    <a href="#"><span class="nav-icon"><svg width="16" height="16" viewBox="0 0 16 16" fill="none" stroke="#2b63ad" stroke-width="1.8"><path d="M8 1l6 3.5v7L8 15l-6-3.5v-7z"/><path d="M2 4.5 8 8l6-3.5M8 8v7"/></svg></span>Labour Code</a>
    <a href="#"><span class="nav-icon"><svg width="6" height="14" viewBox="0 0 6 14" fill="#2b63ad"><circle cx="3" cy="2" r="2"/><rect x="1" y="5" width="4" height="9"/></svg></span>Personal Information</a>
    <a href="#"><span class="nav-icon"><svg width="18" height="12" viewBox="0 0 18 12"><path d="M1 6q8-10 16 0-8 10-16 0z" fill="none" stroke="#2b63ad" stroke-width="1.8"/><circle cx="9" cy="6" r="2.8" fill="#2b63ad"/></svg></span>Appraisal and Review</a>
    <a href="#"><span class="nav-icon"><svg width="16" height="16" viewBox="0 0 16 16" fill="none" stroke="#2b63ad" stroke-width="1.8"><path d="M7 2H2v12h12V9"/><path d="M12 1.5l2.5 2.5L8 10.5H5.5V8z"/></svg></span>Write Up-Slip</a>
    <a href="#"><span class="nav-icon"><svg width="14" height="16" viewBox="0 0 14 16" fill="#2b63ad"><circle cx="7" cy="4" r="3.5"/><path d="M0 16q0-7 7-7t7 7z"/></svg></span>Employee Performance</a>
  </nav>

  <main class="form-panel">
    <div class="form-content">
      <h1 class="form-title">Important! Please read and sign before completing and submitting.</h1>
      <div class="terms">
        <p>I hereby authorize SENTINEL CREST SECURITY to deposit any amounts owed me, as instructed by my employer, by initiating credit entries to my account at the financial institution (hereinafter "Bank.) indicated on this form. Further, I authorize Bank to accept and to credit any credit entries indicated by SENTINEL CREST SECURITY to my account In the even that SENTINEL CREST SECURITY deposits funds erroneously into my account, I authorize SENTINEL CREST SECURITY to debit my account for an amount not to exceed the original amount of the erroneous credit.</p>
        <p>This authorization is to remain in full force and effect until SENTINEL CREST SECURITY and Bank have received written notice from me of its termination in such time and in such manner as to afford SENTINEL CREST SECURITY and Bank reasonable opportunity to act on it.</p>
      </div>
      <div class="sign-row">
        <div class="field"><label>Employee Name:</label><div class="input"></div></div>
        <div class="field"><label>Employee Signature:</label><div class="input"></div></div>
        <div class="field"><label>Sign Date:</label><div class="input"></div></div>
      </div>
      <button class="accept-btn">Accept Document</button>
      <section class="manager-box">
        <h2>ONLY PAYROLL MANAGER SIGNS BELOW</h2>
        <div class="col-left">
          <div class="field"><label>Company Name:</label><div class="input"></div></div>
          <div class="field"><label>Employee File Number:</label><div class="input"></div></div>
        </div>
        <div class="col-right field"><label>Comments:</label><div class="textarea"></div></div>
      </section>
    </div>
    <div class="scrollbar"><span class="arrow up"></span><span class="thumb"></span><span class="arrow down"></span></div>
  </main>

  <footer class="site-footer">Copyright © 2016 Sentinel Crest Security. All Right Reserved</footer>
</body>
</html>
```